Valdane Companies Business Card Design

We need a new business card for our Private Equity Real Estate Development firm, “Valdane” and our EB-5 regional center “Thornmere Regional Center” on one card. We prefer a design that is simple, elegant, and represents the luxury products we design and build as well as the financial security and stability our successful history has produced. We are an industry leader in our field and 3rd generation family business that has evolved into an institutional quality investment platform. Considered design size is standard business card dimensions (3.5 x 2 inches with an additional 1/8 inch space for design elements or backgrounds that extend beyond the finished size of your piece.

Target Market(s)

• High net worth individuals
• Highly skilled technical workers and physicians in the US seeking investment-based immigration opportunities
• Sophisticated private equity investors
• Intermediary partners include domestic attorneys and investment brokers, as well as international agent networks
• US real estate developers

Industry/Entity Type

Finance

Contact Information for Business Card

(Providing placeholder info for personal information, please design for longer character spaces, longer names and addresses etc..)
• Logo for Valdane
• Logo for Thornmere Regional Center
• Full name: Marcus Valdane
• Job title: CEO
• Email address: mvaldane@valdanecompanies.com
• Cell phone number: +1.555.314.2287
• Office number +1.555.628.4410
• Office address: Larkfield Court 5, 4817 Vista Orilla, Calder Point, OR.
• Website: www.valdanecompanies.com

Font styles to use
Serif
Sans Serif

Colors
ec1f27
ffffff
000000

Requirements
Must have
• • Logo for Valdane
• • Logo for Thornmere Regional Center
• - Use rounded corners
• (See .ai file included for logos)
Nice to have
• • Simple, elegant design
• • Aesthetically compatible with our website design (www.valdanecompanies.com)
• • Color palette including but not limited to white, black, and red (as per logos)
Should not have
• - Not too much red color
• - Do not stack both logos on top of each other

```html
<!DOCTYPE html>
<html lang="en">
<head>
<meta charset="utf-8">
<title>Valdane Companies Business Card</title>
<link rel="stylesheet" href="https://fonts.googleapis.com/css2?family=Cinzel:wght@400;700&family=Open+Sans:wght@400;600&display=swap">
<style>
  :root {
    --red: #ec1f27;
    --white: #ffffff;
    --ink: #1a1a1a;
    --logo-grey: #2e2e2e;
    --backdrop: #3b3b3d;
    --card-shadow: rgba(0, 0, 0, 0.35);
  }
  html, body {
    margin: 0;
    padding: 0;
    width: 1200px;
    height: 782px;
    overflow: hidden;
    background: var(--backdrop);
  }
  .stage {
    position: relative;
    width: 1200px;
    height: 782px;
  }
  .card {
    position: absolute;
    width: 560px;
    height: 320px;
    border-radius: 6px;
    overflow: hidden;
    box-shadow: 0 6px 18px var(--card-shadow);
  }

  /* Back side: regional center */
  .card-back {
    left: 580px;
    top: 60px;
    background: var(--red);
    display: flex;
    align-items: center;
    justify-content: center;
  }
  .center-mark {
    display: flex;
    align-items: center;
    gap: 16px;
  }
  .center-mark .square {
    width: 40px;
    height: 40px;
    background: var(--white);
    flex: none;
  }
  .center-mark .divider {
    width: 1px;
    height: 56px;
    background: var(--white);
    flex: none;
  }
  .center-name {
    font-family: "Cinzel", serif;
    font-weight: 700;
    font-size: 24px;
    letter-spacing: 1px;
    color: var(--white);
    margin: 0;
    white-space: nowrap;
  }

  /* Front side: contact */
  .card-front {
    left: 60px;
    top: 400px;
    background: var(--white);
  }
  .holder {
    position: absolute;
    left: 28px;
    top: 26px;
  }
  .holder-name {
    font-family: "Cinzel", serif;
    font-weight: 400;
    font-size: 21px;
    letter-spacing: 0.5px;
    color: var(--ink);
    margin: 0;
  }
  .holder-title {
    font-family: "Open Sans", sans-serif;
    font-size: 11px;
    color: var(--ink);
    margin: 2px 0 0;
  }
  .contact-list {
    position: absolute;
    left: 28px;
    top: 196px;
    margin: 0;
    padding: 0;
    list-style: none;
    font-family: "Open Sans", sans-serif;
    font-size: 14px;
    line-height: 21px;
    color: var(--ink);
  }
  .contact-list li {
    display: flex;
    align-items: center;
    gap: 6px;
    white-space: nowrap;
  }
  .contact-list svg {
    width: 12px;
    height: 12px;
    fill: var(--ink);
    flex: none;
  }
  .firm-mark {
    position: absolute;
    right: 34px;
    top: 92px;
    display: flex;
    flex-direction: column;
    align-items: center;
    gap: 12px;
  }
  .firm-mark .square {
    width: 40px;
    height: 40px;
    background: var(--logo-grey);
  }
  .firm-name {
    font-family: "Cinzel", serif;
    font-weight: 700;
    font-size: 28px;
    letter-spacing: 1px;
    line-height: 34px;
    color: var(--logo-grey);
    margin: 0;
    white-space: nowrap;
  }
  .address {
    position: absolute;
    right: 34px;
    bottom: 26px;
    margin: 0;
    font-family: "Open Sans", sans-serif;
    font-style: normal;
    font-size: 14px;
    line-height: 19px;
    text-align: right;
    color: var(--ink);
  }
  .base-band {
    position: absolute;
    left: 0;
    right: 0;
    bottom: 0;
    height: 10px;
    background: var(--red);
  }
</style>
</head>
<body>
<main class="stage">

  <section class="card card-back" aria-label="Card back">
    <div class="center-mark">
      <span class="square"></span>
      <span class="divider"></span>
      <p class="center-name">Thornmere Regional Center</p>
    </div>
  </section>

  <section class="card card-front" aria-label="Card front">
    <div class="holder">
      <h1 class="holder-name">MARCUS VALDANE</h1>
      <p class="holder-title">CEO</p>
    </div>

    <div class="firm-mark">
      <span class="square"></span>
      <p class="firm-name">VALDANE CAPITAL</p>
    </div>

    <ul class="contact-list">
      <li>
        <svg viewBox="0 0 12 12" aria-hidden="true"><path d="M1 4c0-1.5 2-2.5 5-2.5S11 2.5 11 4v1H8.5V4h-5v1H1zM2.5 6h7l1 4.5h-9z"/></svg>
        +1.555.314.2287
      </li>
      <li>
        <svg viewBox="0 0 12 12" aria-hidden="true"><path d="M3 0.5h6a1 1 0 0 1 1 1v9a1 1 0 0 1-1 1H3a1 1 0 0 1-1-1v-9a1 1 0 0 1 1-1zm0.5 1.5v7h5V2z"/></svg>
        +1.555.628.4410
      </li>
      <li>
        <svg viewBox="0 0 12 12" aria-hidden="true"><path d="M0.5 2.5h11v7h-11zM1.5 3.3v0.5L6 6.7l4.5-2.9v-0.5z"/></svg>
        mvaldane@valdanecompanies.com
      </li>
      <li>
        <svg viewBox="0 0 12 12" aria-hidden="true"><circle cx="6" cy="6" r="5.5"/></svg>
        www.valdanecompanies.com
      </li>
    </ul>

    <address class="address">
      Larkfield Court 5, 4817 Vista<br>
      Orilla, Calder Point, OR
    </address>

    <div class="base-band"></div>
  </section>

</main>
</body>
</html>
```